International Film making Business needs the 5 Logos provided made into a POSTER Format

Design Task:
CREATE A POSTER DESIGN USING THE 5 LOGOS PROVIDED. The BOLD BRIGHT HORIZON LOGO should stand out from the others by being in the middle with the other 4 logos connected to it somehow.

The 5 Businesses already has their 5 Logos, all similar in design to each other.

BOLD BRIGHT HORIZON is the Main Logo that encompasses the other 4 Logos. So it must stand out more and it is like the Overall Business entity that incorporates the other 4 Logos.

What is required is that by using the 5 Logo designs provided, create a cool graphic artwork that somehow incorporates ALL of the 5 Logos - But having the BOLD BRIGHT HORIZON Logo at the forefront/most important/standing out the most.
- BOLD BRIGHT HORIZON will probably be bigger than the others
- and could be changed into 3D.

I have attached all 5 logos and a hand drawn example of how the BOLD BRIGHT ONWARDS could stand out from the rest.

THE DESIGNS OF THE LOGOS SHOULD NOT BE CHANGED (except the BOLDBRIGHTHORIZON which can be 3D)

Please do not be restricted with the sample idea. Creativity is encouraged

DIMENSION: 3000 mm x 6000 mm
high resolution graphic

Logo Text

bold bright , bold bright pictures, bold bright legends, bold bright groovy, BOLD BRIGHT ONWARDS

Requirements
Must have
• USE THE 5 LOGOS PROVIDED ONLY - Only BOLD BRIGHT HORIZON can be changed into 3D only
Nice to have
• Eye catching design, showing the Bold Bright Horizon as the most powerful Logo that has the other 4 as subordinate companies
Should not have
• ANY CHANGE IN THE 5 LOGO DESIGNS (EXcept 3D for Bold Bright Horizons)

```html
<!DOCTYPE html>
<html lang="en">
<head>
<meta charset="utf-8">
<title>Bold Bright Onwards – Group Poster</title>
<link rel="stylesheet" href="https://fonts.googleapis.com/css2?family=Marcellus&family=Montserrat:wght@300&display=swap">
<style>
  :root {
    --gold-dark: #b07a26;
    --gold-mid: #d4a54a;
    --gold-light: #f6e7a8;
    --black: #000000;
    --url-grey: #9a9a9a;
    --blue-brand: #2a8fd8;
    --grey-brand: #a8a8a8;
    --legend-brand: #e9782a;
    --green-brand: #2f9a3e;
  }
  * { margin: 0; padding: 0; box-sizing: border-box; }
  html, body { width: 1200px; height: 600px; overflow: hidden; background: var(--black); }
  .poster {
    position: relative;
    width: 1200px;
    height: 600px;
    background: linear-gradient(90deg, var(--gold-dark) 0%, var(--gold-mid) 30%, var(--gold-light) 55%, var(--gold-mid) 80%, var(--gold-dark) 100%);
    overflow: hidden;
  }
  .hero {
    position: absolute;
    left: 18px; top: 18px;
    width: 1164px; height: 262px;
    background: var(--black);
  }
  .hero-mark {
    position: absolute;
    left: 300px; top: 50px;
    width: 160px; height: 160px;
    border-radius: 50%;
    background: var(--gold-mid);
  }
  .hero-name {
    position: absolute;
    left: 506px; top: 78px;
    font-family: "Marcellus", serif;
    font-weight: 400;
    font-size: 58px;
    line-height: 72px;
    letter-spacing: 4px;
    color: var(--gold-mid);
    white-space: nowrap;
  }
  .hero-url {
    position: absolute;
    left: 508px; top: 220px;
    font-family: "Montserrat", sans-serif;
    font-weight: 300;
    font-size: 24px;
    letter-spacing: 4px;
    color: var(--url-grey);
    white-space: nowrap;
  }
  .divisions {
    position: absolute;
    left: 18px; top: 280px;
    width: 1164px; height: 302px;
  }
  .divisions svg { display: block; }
  .division-name {
    position: absolute;
    top: 105px;
    width: 220px;
    height: 90px;
    display: flex;
    align-items: center;
    justify-content: center;
    gap: 8px;
    font-family: "Marcellus", serif;
    font-size: 22px;
    line-height: 26px;
    letter-spacing: 1px;
    text-align: left;
    white-space: nowrap;
  }
  .division-name .dot {
    flex: none;
    width: 26px; height: 26px;
    border-radius: 50%;
  }
  .division-core { left: 54px; color: var(--blue-brand); }
  .division-core .dot { background: var(--blue-brand); }
  .division-pictures { left: 332px; color: var(--grey-brand); }
  .division-pictures .dot { background: var(--grey-brand); }
  .division-legends { left: 610px; color: var(--legend-brand); }
  .division-legends .dot { background: var(--legend-brand); }
  .division-groovy { left: 890px; color: var(--green-brand); }
  .division-groovy .dot { background: var(--green-brand); }
</style>
</head>
<body>
<main class="poster">
  <section class="hero">
    <div class="hero-mark" aria-hidden="true"></div>
    <h1 class="hero-name">BOLD BRIGHT<br>ONWARDS</h1>
    <p class="hero-url">boldbrightonwards.example</p>
  </section>

  <section class="divisions">
    <svg width="1164" height="302" viewBox="0 0 1164 302" aria-hidden="true">
      <defs>
        <linearGradient id="band-blue" x1="0" x2="1">
          <stop offset="0" stop-color="#2a3f96"/>
          <stop offset="0.5" stop-color="#1fb3ea"/>
          <stop offset="1" stop-color="#2a3f96"/>
        </linearGradient>
        <linearGradient id="band-grey" x1="0" x2="1">
          <stop offset="0" stop-color="#111"/>
          <stop offset="0.5" stop-color="#8a8a8a"/>
          <stop offset="1" stop-color="#1a1a1a"/>
        </linearGradient>
        <linearGradient id="band-spectrum" x1="0" x2="1">
          <stop offset="0" stop-color="#6a2d91"/>
          <stop offset="0.25" stop-color="#2a3a8f"/>
          <stop offset="0.48" stop-color="#1ea8e0"/>
          <stop offset="0.65" stop-color="#39b54a"/>
          <stop offset="0.85" stop-color="#fff200"/>
          <stop offset="1" stop-color="#f15a24"/>
        </linearGradient>
        <linearGradient id="band-green" x1="0" x2="1">
          <stop offset="0" stop-color="#0a6b3a"/>
          <stop offset="0.5" stop-color="#8dc63f"/>
          <stop offset="1" stop-color="#0a6b3a"/>
        </linearGradient>
        <linearGradient id="frame-gold" x1="0" y1="0" x2="1" y2="1">
          <stop offset="0" stop-color="#b07a26"/>
          <stop offset="0.45" stop-color="#f6e7a8"/>
          <stop offset="1" stop-color="#b07a26"/>
        </linearGradient>
      </defs>
      <rect x="0" y="0" width="303" height="302" fill="url(#band-blue)"/>
      <rect x="303" y="0" width="275" height="302" fill="url(#band-grey)"/>
      <rect x="578" y="0" width="280" height="302" fill="url(#band-spectrum)"/>
      <rect x="858" y="0" width="306" height="302" fill="url(#band-green)"/>

      <g class="diamond-frames">
        <polygon points="164,3 311,150 164,297 17,150" fill="url(#frame-gold)"/>
        <polygon points="164,21 293,150 164,279 35,150" fill="#000"/>
        <polygon points="442,3 589,150 442,297 295,150" fill="url(#frame-gold)"/>
        <polygon points="442,21 571,150 442,279 313,150" fill="#000"/>
        <polygon points="720,3 867,150 720,297 573,150" fill="url(#frame-gold)"/>
        <polygon points="720,21 849,150 720,279 591,150" fill="#000"/>
        <polygon points="1000,3 1147,150 1000,297 853,150" fill="url(#frame-gold)"/>
        <polygon points="1000,21 1129,150 1000,279 871,150" fill="#000"/>
      </g>
    </svg>

    <div class="division-name division-core"><span class="dot"></span><span>BOLD<br>BRIGHT</span></div>
    <div class="division-name division-pictures"><span class="dot"></span><span>BOLD BRIGHT<br>PICTURES</span></div>
    <div class="division-name division-legends"><span class="dot"></span><span>BOLD BRIGHT<br>LEGENDS</span></div>
    <div class="division-name division-groovy"><span class="dot"></span><span>BOLD BRIGHT<br>GROOVY</span></div>
  </section>
</main>
</body>
</html>
```